Online business manager needs a website

I need a website designed and then coded. I am an online business manager serving a number of different industries providing administrative support to existing small businesses and helping solo practitioners get their new business up and running.

I didn't have a logo formally designed but have been using the attached avatar and wouldn't mind something that incorporated that.

The business doesn't have an official name, so I've just been using my name Lena Morvath, Online Business Manager or Lena Morvath, OBM. I've attached two documents that I have made previously for an example of content.

I would prefer the final site be in Wordpress.

Requirements
Must have
• A way to contact me, testimonials, list of services

```html
<!DOCTYPE html>
<html lang="en">
<head>
<meta charset="utf-8">
<title>Lena Morvath – Online Business Manager</title>
<link href="https://fonts.googleapis.com/css2?family=Poppins:wght@300;400;500;600;700&family=Roboto+Condensed:wght@300;400&display=swap" rel="stylesheet">
<style>
:root{
  --navy:#090c2c;
  --navy-2:#121a52;
  --gold:#c8992e;
  --teal:#2ad6cf;
  --ink:#1b1b1b;
  --text:#333;
  --muted:#666;
  --line:#ececec;
  --soft:#f7f7f7;
  --white:#fff;
}
*{box-sizing:border-box;margin:0;padding:0}
html,body{width:1200px;height:5068px;overflow:hidden}
body{font-family:"Poppins",sans-serif;color:var(--text);background:var(--white);position:relative}
section,header,footer{position:absolute;left:0;width:1200px}
.abs{position:absolute}

/* Hero */
.hero{top:0;height:580px;background:radial-gradient(ellipse at 70% 85%,#1b3a7a 0%,var(--navy-2) 35%,var(--navy) 75%);overflow:hidden}
.hero-curve{position:absolute;left:0;bottom:0;width:1200px;height:90px}
.brand{left:157px;top:16px;display:flex;align-items:center;gap:12px}
.brand-dot{width:48px;height:48px;border-radius:50%;background:var(--teal);opacity:.85}
.brand-name{font-weight:700;font-size:19px;letter-spacing:1px;color:var(--teal);line-height:1.1;text-transform:uppercase}
.brand-tag{font-size:12px;color:var(--white);font-weight:400}
.nav{top:30px;left:545px;display:flex;gap:30px;align-items:center;font-size:12px;color:var(--white)}
.nav a{color:inherit;text-decoration:none;position:relative}
.nav .active{color:var(--teal)}
.nav .active::after{content:"";position:absolute;left:50%;margin-left:-6px;bottom:-12px;width:12px;height:2px;background:var(--teal)}
.nav .btn-outline{border:1.5px solid var(--teal);border-radius:18px;padding:8px 22px;margin-left:4px}
.hero-first{left:158px;top:148px;font-weight:300;font-size:80px;line-height:1;color:var(--white);letter-spacing:1px}
.hero-last{left:156px;top:222px;font-weight:700;font-size:80px;line-height:1;color:var(--white)}
.hero-badge{left:161px;top:328px;width:313px;height:32px;background:linear-gradient(90deg,#3c50d8,var(--teal));color:var(--white);font-size:14px;letter-spacing:3px;text-align:center;line-height:32px;font-weight:500}
.hero-text{left:161px;top:382px;width:385px;font-size:12.5px;line-height:23px;color:#e6e8f5}
.hero-ring{left:624px;top:102px;width:420px;height:420px;border-radius:50%;border:2px solid #3f7ee0;box-shadow:0 0 18px rgba(80,140,255,.5)}
.hero-photo{left:634px;top:112px;width:400px;height:400px;border-radius:50%;background:radial-gradient(circle at 50% 45%,#e9c9a6 0%,#c89a6d 40%,#6f5a4d 100%)}

/* Section titles */
.title{font-family:"Roboto Condensed",sans-serif;font-weight:400;font-size:44px;color:var(--ink);text-transform:uppercase;letter-spacing:-.5px}
.title span{color:var(--gold)}
.center{width:1200px;left:0;text-align:center}

.card{position:absolute;background:var(--white);box-shadow:0 2px 12px rgba(0,0,0,.12);display:flex;flex-direction:column;align-items:center;justify-content:center;gap:14px;font-size:15px;font-weight:500;color:var(--ink)}
.card svg{width:52px;height:52px;fill:none;stroke:var(--gold);stroke-width:2}
.btn{position:absolute;background:var(--gold);color:var(--white);font-size:13px;text-align:center;line-height:42px;height:42px;width:127px}

/* Services */
.services{top:580px;height:624px}
.svc{width:215px;height:153px}

/* About */
.about{top:1204px;height:694px;background:var(--soft)}
.about-photo{left:0;top:86px;width:557px;height:492px;background:linear-gradient(160deg,#b4427e 0%,#8a2b5a 40%,#5a7a3a 100%)}
.about-photo-top{left:557px;top:86px;width:78px;height:69px;background:linear-gradient(160deg,#8a2b5a,#6d3a4e)}
.about-badge{left:557px;top:155px;width:78px;height:79px;background:var(--gold);display:flex;align-items:center;justify-content:center}
.about-title{left:594px;top:255px}
.about-body{left:594px;top:318px;width:462px;font-size:12.5px;line-height:21px;color:var(--text)}
.about-body p{margin-bottom:12px;text-align:justify}
.about-tag{left:142px;top:618px;width:440px;font-size:14px;font-weight:500;line-height:24px;color:var(--ink)}
.contact-item{display:flex;align-items:center;gap:12px;font-size:12px;color:var(--ink);line-height:19px}
.contact-ico{width:38px;height:38px;border-radius:50%;background:var(--gold);display:flex;align-items:center;justify-content:center}
.contact-ico svg{width:18px;height:18px;fill:none;stroke:var(--white);stroke-width:2}

/* Credentials */
.creds{top:1898px;height:400px}
.cred{width:284px;height:151px;font-size:14px;text-transform:uppercase}

/* Work */
.work{top:2298px;height:938px;background:var(--soft)}
.tile{position:absolute}

/* Rates */
.rates{top:3236px;height:535px}
.rate{width:215px;height:215px;justify-content:flex-start;padding-top:28px;gap:0;text-align:center}
.rate .price{font-size:31px;font-weight:700;color:var(--gold);line-height:40px}
.rate .unit{font-size:14px;font-weight:500;margin-top:8px;padding-bottom:14px;border-bottom:1px solid var(--line);width:175px}
.rate .desc{font-size:14px;font-weight:500;line-height:21px;margin-top:14px}
.rate .note{font-size:12px;font-weight:400;margin-top:12px;color:var(--text)}

/* Testimonial */
.love{top:3771px;height:511px;background:var(--soft)}
.quote-card{left:283px;top:169px;width:634px;height:240px;background:var(--white);box-shadow:0 4px 18px rgba(0,0,0,.1);text-align:center;padding:48px 36px 0;font-size:13px;line-height:22px}
.quote-card p{margin-bottom:12px}
.quote-mark{left:572px;top:145px;width:56px;height:56px;border-radius:50%;background:var(--gold);display:flex;align-items:center;justify-content:center;color:var(--white);font-size:44px;font-weight:700;line-height:1;padding-top:18px}
.q-name{font-weight:600;font-size:15px;color:var(--ink);margin-top:4px}
.q-role{font-size:11px;color:var(--muted)}
.q-arrows{margin-top:8px;display:flex;justify-content:center;gap:8px}
.q-arrows svg{width:20px;height:12px;fill:none;stroke-width:1.6}

/* Contact form */
.quick{top:4282px;height:508px}
.field{position:absolute;background:#f3f3f3;font-size:11px;color:var(--ink);padding:14px 20px}
.quick-photo{left:686px;top:83px;width:372px;height:340px;background:linear-gradient(180deg,#d6d9d4 0%,#e2b870 60%,#e0a82c 100%)}

/* Footer */
.footer{top:4790px;height:278px;background:linear-gradient(100deg,#5b3fc7 0%,#3a7ad8 50%,var(--teal) 100%);color:var(--white)}
.f-brand{left:474px;top:55px;display:flex;align-items:center;gap:12px}
.f-nav{top:162px;left:0;width:1200px;display:flex;justify-content:center;gap:32px;font-size:12px}
.f-nav .active{position:relative}
.f-nav .active::after{content:"";position:absolute;left:50%;margin-left:-6px;bottom:-10px;width:12px;height:2px;background:var(--white)}
.copy{top:250px;width:1200px;text-align:center;font-size:11px}
</style>
</head>
<body>

<header class="hero">
  <div class="abs brand">
    <div class="brand-dot"></div>
    <div><div class="brand-name">Lena Morvath</div><div class="brand-tag">Online Business Manager</div></div>
  </div>
  <nav class="abs nav">
    <a class="active">Home</a><a>About Me</a><a>What I Do Best</a><a>Client Love</a><a class="btn-outline">Contact Me</a>
  </nav>
  <div class="abs hero-first">LENA</div>
  <div class="abs hero-last">MORVATH</div>
  <div class="abs hero-badge">DIGITAL BUSINESS MANAGER</div>
  <p class="abs hero-text">Focused on the live event and entertainment industry. Helping artists and owners to better manage their career and business by strategically reviewing systems, recommending operational efficiencies, and managing inboxes.</p>
  <div class="abs hero-ring"></div>
  <div class="abs hero-photo" role="img" aria-label="Portrait photo of Lena Morvath"></div>
  <svg class="hero-curve" viewBox="0 0 1200 90" preserveAspectRatio="none"><path d="M0 0 Q600 150 1200 0 L1200 90 L0 90 Z" fill="#fff"/></svg>
</header>

<section class="services">
  <h2 class="abs title center" style="top:62px">What I Do <span>Best</span></h2>
  <div class="card svc" style="left:142px;top:140px"><svg viewBox="0 0 52 52"><rect x="8" y="10" width="36" height="26" rx="2"/><path d="M16 44h20M26 36v8M15 18h22M15 24h14"/></svg>Content Repurposing</div>
  <div class="card svc" style="left:375px;top:140px"><svg viewBox="0 0 52 52"><path d="M8 44h36M13 44V32M22 44V26M31 44V20M40 44V14M10 28l10-8 8 4 14-12"/></svg>Financial Analytics</div>
  <div class="card svc" style="left:610px;top:140px"><svg viewBox="0 0 52 52"><rect x="10" y="6" width="28" height="36" rx="2"/><path d="M16 14h16M16 20h16M16 26h10M30 34l8 8 6-6-8-8z"/></svg>Data Entry</div>
  <div class="card svc" style="left:843px;top:140px"><svg viewBox="0 0 52 52"><circle cx="26" cy="8" r="4"/><circle cx="8" cy="20" r="4"/><circle cx="44" cy="20" r="4"/><path d="M12 20h28M26 12v12M20 30l6 16 6-16z"/></svg>Graphic Creations</div>
  <div class="card svc" style="left:258px;top:309px"><svg viewBox="0 0 52 52"><circle cx="26" cy="26" r="14"/><path d="M26 6v6M26 40v6M6 26h6M40 26h6M12 12l4 4M36 36l4 4M12 40l4-4M36 16l4-4"/><rect x="19" y="21" width="14" height="10"/><path d="M19 21l7 6 7-6"/></svg>Email Management</div>
  <div class="card svc" style="left:492px;top:309px"><svg viewBox="0 0 52 52"><circle cx="26" cy="22" r="12"/><path d="M20 36h12M22 42h8M26 6V2M10 22H6M46 22h-4M14 10l-3-3M38 10l3-3"/></svg>Project Management</div>
  <div class="card svc" style="left:726px;top:309px"><svg viewBox="0 0 52 52"><rect x="14" y="4" width="24" height="32" rx="2"/><path d="M20 12h12M20 18h12M8 46h36M12 46V36M22 46V30M32 46V34M42 46V28"/></svg>Bookkeeping</div>
  <div class="btn" style="left:537px;top:498px">Contact Me</div>
</section>

<section class="about">
  <div class="abs about-photo" role="img" aria-label="Photo of Lena Morvath in front of flowering shrubs"></div>
  <div class="abs about-photo-top" role="img" aria-label="Edge of the flowering shrub photo"></div>
  <div class="abs about-badge"><svg width="44" height="40" viewBox="0 0 44 40" fill="none" stroke="#fff" stroke-width="2"><path d="M4 36h36M9 36V26M17 36V20M25 36V24M33 36V14M6 22l10-8 8 4 14-12"/></svg></div>
  <h2 class="abs title about-title">About <span>Me</span></h2>
  <div class="abs about-body">
    <p>I am focused on the live event and entertainment industry. Helping artists and owners to better manage their career and business by strategically reviewing systems, recommending operational efficiencies, &amp; managing inboxes</p>
    <p>Helping businesses achieve their goals is my passion, and I'm thrilled that with my assistance you will have more time for your own passion project. I thrive while working independently, which means you can be confident when leaving tasks for me.</p>
    <p>The type of work that lights me up is anything involving organization and/or spreadsheets. You need data analyzed that includes multiple nested if formulas?</p>
  </div>
  <p class="abs about-tag">You Have An Overwhelming Amount of Email To Sort Through And Appointments To Book? I'm Your Gal!</p>
  <div class="abs contact-item" style="left:667px;top:622px">
    <div class="contact-ico"><svg viewBox="0 0 18 18"><rect x="2" y="4" width="14" height="10"/><path d="M2 4l7 6 7-6"/></svg></div>
    <div>E-mail<br>lena.morvath@mailbox.test</div>
  </div>
  <div class="abs contact-item" style="left:917px;top:622px">
    <div class="contact-ico"><svg viewBox="0 0 18 18"><path d="M4 2l3 4-2 2c1 2 3 4 5 5l2-2 4 3-2 3C8 17 1 10 2 4z"/></svg></div>
    <div>Phone<br>555 014 2287</div>
  </div>
</section>

<section class="creds">
  <div class="card cred" style="left:142px;top:85px"><svg viewBox="0 0 52 52"><path d="M4 18l22-10 22 10-22 10z"/><path d="M14 23v10c6 5 18 5 24 0V23M44 20v14"/><path d="M6 44c8-6 16-6 20 0 4-6 12-6 20 0"/></svg>My Education</div>
  <div class="card cred" style="left:456px;top:85px"><svg viewBox="0 0 52 52"><rect x="6" y="4" width="22" height="12" rx="2"/><circle cx="22" cy="32" r="8"/><circle cx="22" cy="32" r="3"/><circle cx="40" cy="38" r="5"/><path d="M32 10h14v14H34"/></svg>My Skills</div>
  <div class="card cred" style="left:773px;top:85px"><svg viewBox="0 0 52 52"><rect x="6" y="4" width="40" height="26" rx="2"/><path d="M14 12h24M14 18h16"/><circle cx="26" cy="36" r="6"/><path d="M22 41l-2 8 6-3 6 3-2-8"/></svg>My Accreditation</div>
  <div class="btn" style="left:537px;top:276px">Contact Me</div>
</section>

<section class="work">
  <h2 class="abs title center" style="top:76px">My <span>Work</span></h2>
  <div class="tile" style="left:142px;top:159px;width:306px;height:216px;background:linear-gradient(135deg,#fbe7da,#f6d2c2)" role="img" aria-label="Podcast promo graphic with guest portraits"></div>
  <div class="tile" style="left:494px;top:159px;width:564px;height:216px;background:linear-gradient(90deg,#b9c95a 0%,#8fb04a 60%,#2f9bab 68%,#2f9bab 100%)" role="img" aria-label="Animal rescue adoption graphic with a happy dog"></div>
  <div class="tile" style="left:142px;top:401px;width:306px;height:458px;background:linear-gradient(180deg,#ff8d4c 0%,#ff8d4c 56%,#9aa29a 56%,#c6b7a3 100%)" role="img" aria-label="Graphic on simple ways to look great on video calls"></div>
  <div class="tile" style="left:494px;top:401px;width:564px;height:214px;background:linear-gradient(135deg,#eac9cd,#e3bfc3)" role="img" aria-label="Podcast episode cover with headphones and keyboard"></div>
  <div class="tile" style="left:494px;top:641px;width:259px;height:218px;background:#f75f5d" role="img" aria-label="Quote graphic in coral"></div>
  <div class="tile" style="left:795px;top:641px;width:263px;height:218px;background:linear-gradient(135deg,#f6f2e8,#ede5d6)" role="img" aria-label="Podcast guest announcement graphic"></div>
</section>

<section class="rates">
  <h2 class="abs title center" style="top:84px">Rates and <span>Packages</span></h2>
  <div class="card rate" style="left:142px;top:159px"><div class="price">$40</div><div class="unit">Hourly Rate</div><div class="desc">For Clients Needing<br>Only Occasional Help</div></div>
  <div class="card rate" style="left:375px;top:159px"><div class="price">$700</div><div class="unit">20 hours/month</div><div class="desc">Includes One 15 Minute<br>Meeting Per Week</div><div class="note">Responses Within 72 Hours</div></div>
  <div class="card rate" style="left:610px;top:159px"><div class="price">$1,300</div><div class="unit">40 hours/month</div><div class="desc">Includes One 30 Minute<br>Meeting Per Week</div><div class="note">Responses Within 48 Hours</div></div>
  <div class="card rate" style="left:843px;top:159px"><div class="price">$2,400</div><div class="unit">80 hours/month</div><div class="desc">Includes One 60 Minute<br>Meeting Per Week</div><div class="note">Responses Within 24 Hours</div></div>
  <div class="btn" style="left:534px;top:413px">Get Started</div>
</section>

<section class="love">
  <h2 class="abs title center" style="top:76px">Clients <span>Love</span></h2>
  <div class="abs quote-card">
    <p>When it became apparent that a project would take more time than I had, Lena stepped up to take on the required research.</p>
    <p>She was thorough and timely; able to meet a last-minute 12-hour deadline. I would highly recommend Lena to assist with your next project.</p>
    <div class="q-name">Dana R.</div>
    <div class="q-role">Owner, Ridgeline Roofing</div>
    <div class="q-arrows">
      <svg viewBox="0 0 20 12" stroke="#333"><path d="M19 6H2M7 1L2 6l5 5"/></svg>
      <svg viewBox="0 0 20 12" stroke="#c8992e"><path d="M1 6h17M13 1l5 5-5 5"/></svg>
    </div>
  </div>
  <div class="abs quote-mark">&#8220;</div>
</section>

<section class="quick">
  <h2 class="abs title" style="left:140px;top:96px">Quick <span>Me</span></h2>
  <div class="field" style="left:142px;top:152px;width:226px;height:45px">First Name*</div>
  <div class="field" style="left:382px;top:152px;width:226px;height:45px">Latest Name*</div>
  <div class="field" style="left:142px;top:211px;width:226px;height:45px">Email*</div>
  <div class="field" style="left:382px;top:211px;width:226px;height:45px">Phone*</div>
  <div class="field" style="left:142px;top:272px;width:466px;height:88px">Message</div>
  <div class="btn" style="left:142px;top:384px">Submit Now</div>
  <div class="abs quick-photo" role="img" aria-label="Portrait photo of Lena Morvath in a yellow top"></div>
</section>

<footer class="footer">
  <div class="abs f-brand">
    <div class="brand-dot" style="background:#fff;opacity:.9"></div>
    <div><div class="brand-name" style="color:#fff">Lena Morvath</div><div class="brand-tag">Online Business Manager</div></div>
  </div>
  <nav class="abs f-nav"><span class="active">Home</span><span>About Me</span><span>What I Do Best</span><span>Client Love</span><span>Contact Me</span></nav>
  <div class="abs copy">© 2023 Lena Morvath. All Rights Reserved.</div>
</footer>

</body>
</html>
```